Test and Tag business card design

We are an appliance test and tag company in Brisbane Australia requiring a business card design.
I don't have a logo.
Card front: Matte black background with white font.
Card back: White background with black font colour
Examples are attached
Minimalist design
Reason: Looking for more designs with an extreme minimal feel
Industry/Entity Type
Appliance
Contact Information for Business Card
Business name: Norvane Check and Label
Description: Onsite Electrical Testing and Tagging
Licence No. 41823
Name: Greg Palwick
Mobile: 0419 286 354
Email: greg@norvanecheckandlabel.com.au
Web: norvanecheckandlabel.com.au
Logo Text
Norvane Check and Label
Look and feel

```html
<!DOCTYPE html>
<html lang="en">
<head>
<meta charset="utf-8">
<title>Norvane Check and Label – Business Card</title>
<link rel="stylesheet" href="https://fonts.googleapis.com/css2?family=Audiowide&display=swap">
<style>
  :root {
    --page: #ffffff;
    --card: #000000;
    --ink: #ffffff;
  }
  * { margin: 0; padding: 0; box-sizing: border-box; }
  html, body {
    width: 1200px;
    height: 693px;
    overflow: hidden;
    background: var(--page);
  }
  .card {
    position: absolute;
    left: 20px;
    top: 20px;
    width: 1160px;
    height: 653px;
    background: var(--card);
    color: var(--ink);
    font-family: "Audiowide", sans-serif;
    text-transform: uppercase;
  }
  .brand {
    position: absolute;
    left: 0;
    right: 0;
    top: 70px;
    text-align: center;
  }
  .brand-name {
    font-size: 46px;
    line-height: 1;
    letter-spacing: 0.09em;
    font-weight: 400;
  }
  .brand-tagline {
    margin-top: 22px;
    font-size: 22px;
    line-height: 1;
    letter-spacing: 0.14em;
    font-weight: 400;
  }
  .divider {
    position: absolute;
    left: 392px;
    top: 183px;
  }
  .person {
    position: absolute;
    left: 0;
    width: 392px;
    top: 322px;
    text-align: center;
    font-size: 40px;
    line-height: 82px;
    letter-spacing: 0.03em;
  }
  .contact {
    position: absolute;
    left: 395px;
    right: 0;
    top: 318px;
    list-style: none;
    text-align: center;
    font-size: 21px;
    line-height: 54px;
    letter-spacing: 0.03em;
  }
  .contact-label { margin-right: 0.45em; }
</style>
</head>
<body>
  <main class="card">
    <header class="brand">
      <h1 class="brand-name">Norvane Check and Label</h1>
      <p class="brand-tagline">Onsite Electrical Testing and Tagging</p>
    </header>

    <svg class="divider" width="4" height="472" viewBox="0 0 4 472" aria-hidden="true">
      <rect x="0" y="0" width="4" height="472" fill="var(--ink)"/>
    </svg>

    <p class="person">Greg<br>Palwick</p>

    <ul class="contact">
      <li><span class="contact-label">Mobile:</span>0419 286 354</li>
      <li><span class="contact-label">Email:</span>greg@norvanecheckandlabel.com.au</li>
      <li><span class="contact-label">Web:</span>norvanecheckandlabel.com.au</li>
    </ul>
  </main>
</body>
</html>
```